I would like some help creating my first business cards for my new business, I am a facilitator of a course that I have created. I am currently starting the sales promotion and marketing part of my business and need some help designing the business cards. Something fairly simple would be good, the core theme of my work is in connection of women to themselves and to each other. My initial design is a tree lit up by lights, a very mother earth type of image. This is not my design however so I probably am not legally able to use the design. I don't have a logo. Could you possibly assist with this?

I would really like to have the following details on the business card:
Meg Donlan
0431 582 917
hi.meg.donlan@larkmail.example

And also the image

Target Market(s)

Women who are living in an isolated environment

Industry/Entity Type

Counsellor

Contact Information for Business Card

Meg Donlan
Facilitator
hi.meg.donlan@larkmail.example
0431 582 917

Font styles to use
Other font styles liked:
• Handwriting - Dakota

Colors
e34197
fee18a
3276b5
33a6d7
33b8a4

Requirements
Must have
• 1) My details as above
• 2) a design (picture) that represents the mother earth theme similar to the designs included in the brief
• 3) no copyright attached to the design
• 4) Colours are very important but it is difficult to describe the colour using the colour wheel. Please refer to the example of the tree that I have included in the drop box.
• 5) I must apologise that I forgot to add the business card needs to have the name of the business in gold letters please: Riverbend Circle Gatherings Collective, thank you
Nice to have
• It would be great to use the tree design that I included in the brief, this is my favourite picture but I think it is probably copyrighted. If it's not, that is the one I would like on my business cards please.

```html
<!DOCTYPE html>
<html lang="en">
<head>
<meta charset="utf-8">
<title>Meg Donlan – Business Card</title>
<link rel="stylesheet" href="https://fonts.googleapis.com/css2?family=Open+Sans:wght@400;700&family=Great+Vibes&display=swap">
<style>
  :root {
    --backdrop: #b9e0d4;
    --sky-edge: #a9dcf7;
    --sky-glow: #f4fbff;
    --blossom: #f7cde6;
    --band-pale: #dcf1fc;
    --name-blue: #1a7fc1;
    --muted-grey: #6b7177;
    --business-gold: #c8962a;
    --icon-blue: #6fb8e0;
    --canopy-green: #5fcf4c;
    --canopy-light: #b7e35a;
  }
  * { margin: 0; padding: 0; box-sizing: border-box; }
  html, body {
    width: 1200px;
    height: 856px;
    overflow: hidden;
    background: var(--backdrop);
  }
  .card {
    position: absolute;
    left: 100px;
    top: 142px;
    width: 1000px;
    height: 571px;
    border-radius: 44px;
    overflow: hidden;
    background: radial-gradient(ellipse 55% 60% at 55% 48%, var(--sky-glow) 0%, #d4effd 55%, var(--sky-edge) 100%);
    box-shadow: 0 18px 40px rgba(40, 90, 80, 0.18);
    font-family: "Open Sans", sans-serif;
  }
  .card__identity {
    position: absolute;
    left: 600px;
    top: 48px;
  }
  .card__name {
    font-weight: 700;
    font-size: 30px;
    color: var(--name-blue);
    line-height: 1.1;
  }
  .card__role {
    font-size: 19px;
    color: var(--muted-grey);
    margin-left: 8px;
  }
  .card__artwork {
    position: absolute;
    left: 95px;
    top: 150px;
    width: 330px;
    height: 350px;
    border-radius: 48% 52% 30% 30% / 55% 55% 25% 25%;
    background: radial-gradient(ellipse 60% 45% at 50% 32%, var(--canopy-light) 0%, var(--canopy-green) 55%, rgba(95, 207, 76, 0.25) 80%, rgba(95, 207, 76, 0) 100%);
  }
  .card__business {
    position: absolute;
    left: 440px;
    top: 205px;
    width: 520px;
    font-family: "Great Vibes", cursive;
    font-size: 52px;
    line-height: 1.15;
    color: var(--business-gold);
    text-align: center;
  }
  .card__base-band {
    position: absolute;
    left: 0;
    right: 0;
    bottom: 0;
    height: 46px;
    background: var(--blossom);
  }
  .card__contact-strip {
    position: absolute;
    left: 290px;
    right: 80px;
    bottom: 0;
    height: 92px;
    border-radius: 26px 26px 0 0;
    background: var(--band-pale);
    display: flex;
    align-items: center;
    justify-content: center;
    gap: 24px;
    font-size: 20px;
    color: var(--muted-grey);
    padding: 6px 20px 0;
  }
  .contact-item {
    display: flex;
    align-items: center;
    gap: 10px;
    white-space: nowrap;
  }
  .contact-item svg { width: 22px; height: 22px; flex: none; }
</style>
</head>
<body>
  <section class="card">
    <div class="card__artwork" role="img" aria-label="Illustration of a woman shaped as a tree, arms raised into a colourful leafy canopy with butterflies, roots spreading below"></div>

    <div class="card__identity">
      <p class="card__name">Meg Donlan</p>
      <p class="card__role">Facilitator</p>
    </div>

    <p class="card__business">Riverbend Circle Gatherings<br>Collective</p>

    <div class="card__base-band"></div>
    <div class="card__contact-strip">
      <span class="contact-item">
        <svg viewBox="0 0 24 24" aria-hidden="true">
          <circle cx="12" cy="12" r="11" fill="var(--icon-blue)"/>
          <path d="M8.2 6.5l2 2.2-1.1 1.4c.7 1.6 2 2.9 3.6 3.7l1.4-1.1 2.2 2-1.2 1.7c-3.6-.6-7.3-4.3-7.9-7.9z" fill="#fff"/>
        </svg>
        0431 582 917
      </span>
      <span class="contact-item">
        <svg viewBox="0 0 24 24" aria-hidden="true">
          <circle cx="12" cy="12" r="11" fill="var(--icon-blue)"/>
          <rect x="6.5" y="8" width="11" height="8" rx="1" fill="#fff"/>
          <path d="M6.8 8.5l5.2 4 5.2-4" fill="none" stroke="var(--icon-blue)" stroke-width="1.2"/>
        </svg>
        hi.meg.donlan@larkmail.example
      </span>
    </div>
  </section>
</body>
</html>
```